Refresh Brightpath Coursecraft

Need a new design for e-learning development and web app development site: http://brightpathcoursecraft.example. Need pages for everything on menu bar plus a training services and a web app development services pages and a better page for samples http://brightpathcoursecraft.example/samples5/.

***Must be programmed in html 5. NO CMS. No WP. No Plume. Straight html/css.

Target Market(s)

government

Industry/Entity Type

Government

Coding

Coded - Design and coding required

Number of Pages Required

1 page

Requirements
Must have
• Must be coded in html5/css. No CMS.
• Divided so you can easily see that we offer 3 separate services:
• Live Training - E-Learning Development - Web App Development
• A way to display logos of all our clients like on bottom of this page: https://www.quorvatests.example (this is also our website so you can copy all these logos)
• List both our Denver location which is already on our website plus our office in Velmoro Plaza. Street 62 Sur, 14-87. Medellín, Antioquia.
• A page like this for our web app dev services https://www.tekvanu.example/product-development
Should not have
• CMS

```html
<!DOCTYPE html>
<html lang="en">
<head>
<meta charset="utf-8">
<title>Brightpath Coursecraft</title>
<link href="https://fonts.googleapis.com/css2?family=Montserrat:wght@400;600;700&family=Open+Sans:wght@400;600;700&display=swap" rel="stylesheet">
<style>
:root{
  --blue:#1f6fb2;
  --blue-dark:#175a93;
  --orange:#f39a1e;
  --ink:#1d1d1d;
  --text:#444;
  --grey:#f2f2f2;
  --white:#fff;
}
*{margin:0;padding:0;box-sizing:border-box}
html,body{width:1200px;height:4027px;overflow:hidden;background:var(--white)}
body{position:relative;font-family:"Open Sans",sans-serif;color:var(--text)}
a{text-decoration:none}
.abs{position:absolute}
h2,.brand,.hero-title{font-family:"Montserrat",sans-serif}

/* header */
.site-header{position:absolute;top:0;left:0;width:1200px;height:102px;background:var(--white)}
.brand{position:absolute;left:110px;top:28px;display:flex;align-items:center;gap:12px;color:var(--blue);font-weight:700;font-size:22px;line-height:1;white-space:nowrap}
.brand-dot{width:46px;height:46px;border-radius:50%;background:var(--orange);flex:none}
.nav{position:absolute;top:42px;left:520px;display:flex;font-family:"Open Sans",sans-serif;font-weight:600;font-size:15px;color:var(--ink)}
.nav a{color:inherit;display:inline-block;padding:0 22px;position:relative}
.nav a.active{color:var(--blue)}
.nav a.active::after{content:"";position:absolute;left:12px;right:12px;bottom:-12px;height:14px;border:2px solid var(--blue);border-top:none;border-radius:0 0 50% 50%}

/* hero */
.hero{position:absolute;top:102px;left:0;width:1200px;height:710px}
.hero-photo{position:absolute;inset:0;background:linear-gradient(120deg,#6b5a4c 0%,#4a3b31 40%,#2f2823 70%,#8a8680 100%)}
.hero-curve{position:absolute;left:0;bottom:0;width:1200px;height:160px}
.hero-title{position:absolute;top:222px;width:100%;text-align:center;color:var(--white);font-weight:600;font-size:62px;line-height:76px;letter-spacing:3px;white-space:nowrap}
.hero-sub{position:absolute;top:304px;width:100%;text-align:center;color:var(--white);font-size:27px;line-height:36px;white-space:nowrap}
.btn{display:inline-block;background:var(--blue);color:var(--white);font-weight:700;font-size:17px;border-radius:30px;text-align:center;text-transform:uppercase}
.hero .btn{position:absolute;left:502px;top:380px;width:196px;height:58px;line-height:58px}

/* welcome */
.welcome-mark{left:565px;top:858px;width:70px;height:70px;border-radius:50%;background:var(--blue)}
.welcome h2{position:absolute;top:938px;width:100%;text-align:center;font-size:38px;line-height:48px;font-weight:700;color:var(--ink)}
h2 .accent{color:var(--orange)}
.welcome p{position:absolute;left:148px;width:904px;text-align:center;font-size:16.5px;line-height:32px}
.welcome .btn{position:absolute;left:460px;top:1277px;width:280px;height:60px;line-height:60px;font-size:16px}

/* services */
.service{position:absolute;left:0;width:1200px}
.service.light{background:var(--grey)}
.service.dark{background:linear-gradient(135deg,#2a7fc2 0%,#1f6fb2 55%,#165b96 100%);color:var(--white)}
.service-circle{position:absolute;width:332px;height:332px;border-radius:50%;background:var(--white);border-bottom:8px solid var(--blue);box-shadow:0 6px 14px rgba(0,0,0,.12)}
.service-icon{position:absolute;left:96px;top:96px;width:140px;height:130px;border-radius:8px;background:var(--orange)}
.service h2{position:absolute;font-size:38px;line-height:48px;font-weight:700;color:var(--ink);white-space:nowrap}
.service.dark h2{color:var(--white)}
.service p{position:absolute;width:540px;font-size:16.5px;line-height:32px}

/* clients */
.clients h2{position:absolute;top:3054px;width:100%;text-align:center;font-size:38px;line-height:48px;font-weight:700;color:var(--ink)}
.logo-row{position:absolute;left:100px;width:1000px;display:flex;justify-content:space-between;align-items:center}
.client{display:flex;align-items:center;gap:8px;font-family:"Open Sans",sans-serif;font-weight:700;font-size:15px;color:#3a3a3a;white-space:nowrap}
.client .seal{width:66px;height:66px;border-radius:50%;background:#c9b98a}
.client .sq{width:30px;height:30px;background:var(--blue)}

/* footer */
.site-footer{position:absolute;top:3598px;left:0;width:1200px;height:429px;background:linear-gradient(135deg,#2b80c4 0%,#1f6fb2 55%,#1a62a0 100%);color:var(--white)}
.site-footer .brand{left:110px;top:140px;color:var(--white);font-size:18px;line-height:22px}
.site-footer .brand-dot{background:var(--white)}
.foot-col{position:absolute;font-size:15px;line-height:30px}
.foot-col h3{font-family:"Open Sans",sans-serif;font-size:22px;font-weight:700;margin-bottom:14px}
.foot-line{display:flex;align-items:flex-start;gap:8px;white-space:nowrap}
.foot-line svg{flex:none;margin-top:8px}
.socials{display:flex;gap:10px;margin-top:12px}
.socials span{width:42px;height:42px;border-radius:50%;background:var(--white)}
.copyright{position:absolute;top:375px;width:100%;text-align:center;font-size:15px}
</style>
</head>
<body>

<header class="site-header">
  <div class="brand"><span class="brand-dot"></span>BRIGHTPATH COURSECRAFT</div>
  <nav class="nav">
    <a class="active" href="#">HOME</a>
    <a href="#">ABOUT US</a>
    <a href="#">OUR SERVICES</a>
    <a href="#">PARTNERS</a>
    <a href="#">CONTACT US</a>
  </nav>
</header>

<section class="hero">
  <div class="hero-photo" role="img" aria-label="Photo of a student writing notes at a desk beside a laptop"></div>
  <div class="hero-title">BRIGHTPATH COURSECRAFT</div>
  <div class="hero-sub">We are a e-learning development and web app development</div>
  <a class="btn" href="#">Get Started</a>
  <svg class="hero-curve" viewBox="0 0 1200 160" preserveAspectRatio="none">
    <path d="M0 10 Q600 230 1200 10 L1200 160 L0 160 Z" fill="#fff"/>
    <path d="M0 10 Q600 230 1200 10" fill="none" stroke="#1f6fb2" stroke-width="6"/>
  </svg>
</section>

<section class="welcome">
  <div class="abs welcome-mark"></div>
  <h2>Welcome to <span class="accent">Brightpath Coursecraft</span></h2>
  <p style="top:1010px">Lorem ipsum dolor sit amet, consectetur adipiscing elit, sed do eiusmod tempor incididunt ut labore et dolore magna aliqua. Ut enim ad minim veniam, quis nostrud exercitation ullamco laboris nisi ut aliquip ex ea commodo consequat. Duis aute irure dolor in reprehenderit in voluptate velit esse cillum dolore eu fugiat nulla pariatur. Excepteur sint occaecat cupidatat non proident, sunt in culpa qui officia deserunt mollit anim id est laborum.</p>
  <p style="top:1160px">Sed ut perspiciatis unde omnis iste natus error sit voluptatem accusantium doloremque laudantium, totam rem aperiam, eaque ipsa quae ab illo inventore veritatis et quasi architecto beatae vitae dicta sunt explicabo</p>
  <a class="btn" href="#">Read More Information</a>
</section>

<section class="service light" style="top:1439px;height:494px">
  <div class="service-circle" style="left:111px;top:68px">
    <div class="service-icon" role="img" aria-label="Icon of a trainer presenting to a group"></div>
  </div>
  <h2 style="left:521px;top:116px">Live <span class="accent">Training Services</span></h2>
  <p style="left:521px;top:186px">Lorem ipsum dolor sit amet, consectetur adipiscing elit, sed do eiusmod tempor incididunt ut labore et dolore magna aliqua. Ut enim ad minim veniam, quis nostrud exercitation ullamco laboris nisi ut aliquip ex ea commodo consequat. Duis aute irure dolor in reprehenderit in voluptate velit esse cillum dolore eu fugiat nulla pariatur.</p>
</section>

<section class="service dark" style="top:1933px;height:518px">
  <h2 style="left:110px;top:132px">E-Learning <span class="accent">Development</span></h2>
  <p style="left:110px;top:210px;width:570px;font-size:15.5px">Sed ut perspiciatis unde omnis iste natus error sit voluptatem accusantium doloremque laudantium, totam rem aperiam, eaque ipsa quae ab illo inventore veritatis et quasi architecto beatae vitae dicta sunt explicabo. Nemo enim ipsam voluptatem quia voluptas sit aspernatur aut odit aut fugit, sed quia consequuntur magni dolores eos qui ratione voluptatem sequi nesciunt.</p>
  <div class="service-circle" style="left:755px;top:84px">
    <div class="service-icon" role="img" aria-label="Icon of a person working at a desk"></div>
  </div>
</section>

<section class="service light" style="top:2451px;height:521px">
  <div class="service-circle" style="left:111px;top:95px">
    <div class="service-icon" role="img" aria-label="Icon of desktop, tablet and phone screens"></div>
  </div>
  <h2 style="left:521px;top:140px">Web <span class="accent">App Development</span></h2>
  <p style="left:521px;top:210px;font-size:15.5px">At vero eos et accusamus et iusto odio dignissimos ducimus qui blanditiis praesentium voluptatum deleniti atque corrupti quos dolores et quas molestias excepturi sint occaecati cupiditate non provident, similique sunt in culpa qui officia deserunt mollitia animi, id est laborum et dolorum fuga. Et harum quidem rerum facilis est et expedita distinctio.</p>
</section>

<section class="clients">
  <h2>Our <span class="accent">Clients Partner</span></h2>
  <div class="logo-row" style="top:3168px">
    <span class="client">Skyward Corps</span>
    <span class="client"><span class="seal" style="background:#1f3d7a"></span></span>
    <span class="client"><span class="seal"></span></span>
    <span class="client"><span class="seal" style="background:#23407a;border-radius:10px"></span></span>
    <span class="client"><span class="seal" style="background:#7a2b2b"></span></span>
    <span class="client">Clearwave</span>
    <span class="client"><span class="sq" style="background:#2e8b3e"></span>Verdalis</span>
    <span class="client"><span class="sq" style="background:#b33"></span></span>
  </div>
  <div class="logo-row" style="top:3296px">
    <span class="client"><span class="seal" style="background:#2b3b5c"></span></span>
    <span class="client"><span class="sq" style="background:#2e6b4a"></span>Oakmere</span>
    <span class="client"><span class="sq" style="background:#1e5a2e"></span>Northfield University</span>
    <span class="client">Tessalon Bio</span>
    <span class="client"><span class="seal" style="background:#4a7ab8"></span></span>
    <span class="client"><span class="seal" style="background:#9c3a3a"></span></span>
  </div>
  <div class="logo-row" style="top:3425px">
    <span class="client"><span class="seal" style="background:#3b4f8a"></span></span>
    <span class="client">Prairie State</span>
    <span class="client">Highcrest U</span>
    <span class="client"><span class="seal" style="background:#8a2a1e"></span></span>
    <span class="client">Ember Guard</span>
    <span class="client"><span class="seal" style="background:#9a9a9a"></span></span>
    <span class="client" style="font-size:26px;color:#1f6fb2">LUMORA</span>
  </div>
</section>

<footer class="site-footer">
  <div class="brand"><span class="brand-dot"></span><span>BRIGHTPATH<br>COURSECRAFT</span></div>
  <div class="foot-col" style="left:458px;top:90px;width:360px">
    <h3>LOCATION</h3>
    <div class="foot-line"><svg width="12" height="16" viewBox="0 0 12 16"><path d="M6 0a6 6 0 0 0-6 6c0 4.5 6 10 6 10s6-5.5 6-10a6 6 0 0 0-6-6zm0 8.5A2.5 2.5 0 1 1 6 3.5a2.5 2.5 0 0 1 0 5z" fill="#fff"/></svg><span>5820 E 9th Avenue, Suite 2-115<br>Aurora, CO. 80010</span></div>
    <div class="foot-line" style="margin-top:18px"><svg width="14" height="14" viewBox="0 0 14 14"><path d="M3 0l2.5 3.5-1.5 2a8 8 0 0 0 4.5 4.5l2-1.5L14 11l-2 3C5.5 14 0 8.5 0 2z" fill="#fff"/></svg><span>Telephone: +1 555 014 7720</span></div>
    <div class="foot-line" style="margin-top:18px;font-size:14px"><svg width="14" height="11" viewBox="0 0 14 11"><path d="M0 0h14v11H0z" fill="#fff"/><path d="M0 0l7 6 7-6" fill="none" stroke="#1f6fb2" stroke-width="1.5"/></svg><span>Email:support@brightpathcoursecraft.example</span></div>
  </div>
  <div class="foot-col" style="left:842px;top:90px;width:300px">
    <h3>OUR OFFICE</h3>
    <div>Velmoro Plaza. Street 62 Sur, 14-87.<br>Medellín, Antioquia.</div>
    <h3 style="margin-top:12px;margin-bottom:0">GET IN TOUCH</h3>
    <div class="socials"><span aria-label="Social link"></span><span aria-label="Social link"></span><span aria-label="Social link"></span></div>
  </div>
  <div class="copyright">Copyrights © 2019 Brightpath Coursecraft. All rights reserved.</div>
</footer>

</body>
</html>
```